Veldmark Supplies Business Card

Professional business card that stand out to our potential customers. Front and back with clean modern design

Industry/Entity Type

Oil and gas

Contact Information for Business Card

Name, address, website , office phone and cell number

Requirements
Must have
• Editable files for each employee

```html
<!DOCTYPE html>
<html lang="en">
<head>
<meta charset="utf-8">
<title>Veldmark Supplies Business Card</title>
<link href="https://fonts.googleapis.com/css2?family=Montserrat:wght@400;500;800&display=swap" rel="stylesheet">
<style>
  :root {
    --stage: #3a3a3a;
    --sky: #0db0d4;
    --signal-red: #ec1c24;
    --paper: #ffffff;
    --ink: #1a1a1a;
  }
  * { margin: 0; padding: 0; box-sizing: border-box; }
  html, body { width: 1200px; height: 689px; overflow: hidden; }
  body {
    background: var(--stage);
    font-family: "Montserrat", Arial, sans-serif;
    display: flex;
    align-items: center;
    justify-content: center;
    gap: 40px;
  }
  .card {
    position: relative;
    width: 540px;
    height: 309px;
    overflow: hidden;
  }
  .card-front { background: var(--sky); }
  .front-brand {
    position: absolute;
    inset: 0;
    display: flex;
    align-items: center;
    justify-content: center;
    gap: 14px;
  }
  .brand-square {
    width: 34px; height: 34px;
    background: var(--signal-red);
  }
  .front-brand .brand-name {
    color: var(--paper);
    font-weight: 800;
    font-size: 34px;
    text-transform: uppercase;
    letter-spacing: 1px;
  }
  .card-back { background: var(--paper); }
  .back-wave { position: absolute; inset: 0; }
  .back-brand {
    position: absolute;
    left: 26px;
    top: 112px;
    width: 200px;
    display: flex;
    align-items: center;
    gap: 10px;
  }
  .back-brand .brand-square { width: 22px; height: 22px; flex: none; }
  .back-brand .brand-name {
    color: var(--signal-red);
    font-weight: 800;
    font-size: 19px;
    line-height: 1.1;
    text-transform: uppercase;
  }
  .contact {
    position: absolute;
    left: 292px;
    top: 34px;
    color: var(--ink);
    font-size: 12px;
    line-height: 1.35;
  }
  .contact-name {
    color: var(--signal-red);
    font-weight: 800;
    font-size: 21px;
    text-transform: uppercase;
    line-height: 1.1;
  }
  .contact-title { font-size: 12.5px; margin-bottom: 10px; }
  .contact-address { margin-bottom: 8px; }
  .contact-list { list-style: none; }
  .contact-list li {
    display: flex;
    align-items: center;
    gap: 8px;
    margin-bottom: 3px;
  }
  .icon { width: 15px; height: 15px; flex: none; }
  .accent { color: var(--signal-red); }
</style>
</head>
<body>
  <section class="card card-front">
    <div class="front-brand">
      <span class="brand-square"></span>
      <span class="brand-name">Veldmark Supplies</span>
    </div>
  </section>

  <section class="card card-back">
    <svg class="back-wave" width="540" height="309" viewBox="0 0 540 309">
      <path d="M0 300 C120 250 260 230 360 190 C440 160 510 120 540 60 L540 309 L0 309 Z" fill="var(--sky)"/>
      <path d="M0 300 C120 250 260 230 360 190 C440 160 510 120 540 60" fill="none" stroke="var(--signal-red)" stroke-width="3"/>
      <line x1="244" y1="40" x2="262" y2="226" stroke="var(--sky)" stroke-width="1.5"/>
      <line x1="256" y1="70" x2="268" y2="196" stroke="var(--signal-red)" stroke-width="1.5"/>
      <line x1="264" y1="30" x2="280" y2="180" stroke="var(--signal-red)" stroke-width="1.5"/>
    </svg>

    <div class="back-brand">
      <span class="brand-square"></span>
      <span class="brand-name">Veldmark<br>Supplies</span>
    </div>

    <div class="contact">
      <p class="contact-name">Tobin Halversen</p>
      <p class="contact-title">President</p>
      <p class="contact-address">482 Larkspur Ave, Ste<br>210, Orrin, TX 79015</p>
      <ul class="contact-list">
        <li>
          <svg class="icon" viewBox="0 0 15 15"><rect width="15" height="15" rx="2" fill="var(--signal-red)"/><path d="M4 5 Q7.5 2.5 11 5 L10 6.5 L8.8 6 V5.2 H6.2 V6 L5 6.5 Z M4.5 8 H10.5 V11 H4.5 Z" fill="#fff"/></svg>
          <span>555-014-3827</span>
        </li>
        <li>
          <svg class="icon" viewBox="0 0 15 15"><rect width="15" height="15" rx="2" fill="var(--signal-red)"/><rect x="5" y="3" width="5" height="9" rx="1" fill="none" stroke="#fff" stroke-width="1.2"/></svg>
          <span>000-000-9999</span>
        </li>
        <li>
          <svg class="icon" viewBox="0 0 15 15"><rect width="15" height="15" rx="2" fill="var(--signal-red)"/><rect x="3" y="4.5" width="9" height="6" fill="none" stroke="#fff" stroke-width="1.1"/><path d="M3 4.5 L7.5 8 L12 4.5" fill="none" stroke="#fff" stroke-width="1.1"/></svg>
          <span>info@example-youremail.com</span>
        </li>
        <li>
          <svg class="icon" viewBox="0 0 15 15"><rect width="15" height="15" rx="2" fill="var(--signal-red)"/><circle cx="7.5" cy="7.5" r="4" fill="none" stroke="#fff" stroke-width="1.1"/><path d="M3.5 7.5 H11.5 M7.5 3.5 V11.5" stroke="#fff" stroke-width="0.9"/></svg>
          <span>www.<span class="accent">example-yourwebsite</span>.com</span>
        </li>
      </ul>
    </div>
  </section>
</body>
</html>
```